Quorva - corporate Business Card

We need a good look and innovative business card for a new start up company based in Los Angeles called "Quorva". We are in a payment business, including payment card, app, and ewallet. We are expert in online payment and Card not present (CNP) transaction.
We need an innovative, modern business card.

Our logo font is Aero Matics

Target Market(s)

Startup - Bank - Online Payment - Card Manufacturing

Industry/Entity Type

Startup

Contact Information for Business Card

phone: 555 014 7396 - Address: 4172 Marlowe blvd, Fenwick Bay, OR 97411

Requirements
Must have
• Message: innovative, professional, expert, high tech, trust, online payment expert, security
Nice to have
• no comment
Should not have
• no Comment

```html
<!DOCTYPE html>
<html lang="en">
<head>
<meta charset="utf-8">
<title>Quorva – Business Card</title>
<link rel="stylesheet" href="https://fonts.googleapis.com/css2?family=Montserrat:wght@500;600;700;800&display=swap">
<style>
  :root {
    --brand-red: #b71f31;
    --card-white: #ffffff;
    --stage: #2b2b2e;
    --text-font: "Montserrat", Arial, sans-serif;
  }
  * { box-sizing: border-box; margin: 0; padding: 0; }
  html, body {
    width: 1200px; height: 900px; overflow: hidden;
    background: var(--stage);
    font-family: var(--text-font);
  }
  .stage { position: relative; width: 1200px; height: 900px; }
  .card {
    position: absolute; left: 250px; width: 700px; height: 400px;
    border-radius: 28px; overflow: hidden;
  }
  /* Front side */
  .card-front { top: 35px; background: var(--brand-red); }
  .front-halo {
    position: absolute; left: 170px; top: 10px; width: 380px; height: 380px;
    border-radius: 50%; background: rgba(255,255,255,0.09);
  }
  .front-dot {
    position: absolute; left: 70px; top: 140px; width: 150px; height: 150px;
    border-radius: 50%; background: var(--card-white);
  }
  .front-wordmark {
    position: absolute; left: 240px; top: 150px;
    font-size: 104px; font-weight: 700; color: var(--card-white);
    letter-spacing: 1px; line-height: 1;
  }
  /* Back side */
  .card-back { top: 465px; background: var(--card-white); }
  .back-shapes { position: absolute; inset: 0; }
  .back-wordmark {
    position: absolute; left: 40px; top: 55px;
    font-size: 56px; font-weight: 700; color: var(--brand-red); line-height: 1;
  }
  .holder { position: absolute; left: 44px; top: 135px; color: var(--brand-red); }
  .holder-name { font-size: 24px; font-weight: 800; }
  .holder-title { font-size: 15px; font-weight: 600; margin-top: 2px; }
  .contact-list {
    position: absolute; left: 44px; top: 262px; list-style: none;
    color: var(--card-white); font-size: 16px; font-weight: 500;
  }
  .contact-list li { display: flex; align-items: center; gap: 12px; height: 24px; }
  .contact-list svg { width: 14px; height: 14px; fill: var(--card-white); flex: none; }
  .address {
    position: absolute; left: 44px; top: 340px;
    color: var(--card-white); font-size: 17px; font-weight: 600; line-height: 1.3;
    font-style: normal;
  }
</style>
</head>
<body>
<main class="stage">
  <section class="card card-front" aria-label="Card front">
    <div class="front-halo"></div>
    <div class="front-dot"></div>
    <div class="front-wordmark">quorva</div>
  </section>

  <section class="card card-back" aria-label="Card back">
    <svg class="back-shapes" viewBox="0 0 700 400" aria-hidden="true">
      <polygon points="0,235 340,235 430,120 700,120 700,300 575,400 0,400" fill="var(--brand-red)"/>
      <circle cx="590" cy="150" r="100" fill="var(--brand-red)" stroke="var(--card-white)" stroke-width="10"/>
    </svg>
    <div class="back-wordmark">quorva</div>
    <div class="holder">
      <div class="holder-name">Dana Okafor</div>
      <div class="holder-title">President</div>
    </div>
    <ul class="contact-list">
      <li><svg viewBox="0 0 24 24"><path d="M6.6 10.8a15.1 15.1 0 006.6 6.6l2.2-2.2a1 1 0 011-.25 11.4 11.4 0 003.6.6 1 1 0 011 1V20a1 1 0 01-1 1A17 17 0 013 4a1 1 0 011-1h3.5a1 1 0 011 1 11.4 11.4 0 00.6 3.6 1 1 0 01-.25 1z"/></svg>555. 014. 7396</li>
      <li><svg viewBox="0 0 24 24"><path d="M2 5h20v14H2zm2 2v.5l8 5 8-5V7l-8 5z"/></svg>dana@quorva.com</li>
      <li><svg viewBox="0 0 24 24"><path d="M12 2a10 10 0 100 20 10 10 0 000-20zm6.9 9h-3a15 15 0 00-1.3-5.6A8 8 0 0118.9 11zM12 4c.9 1.2 1.8 3.6 1.9 7h-3.8c.1-3.4 1-5.8 1.9-7zM9.4 5.4A15 15 0 008.1 11h-3a8 8 0 014.3-5.6zM5.1 13h3a15 15 0 001.3 5.6A8 8 0 015.1 13zM12 20c-.9-1.2-1.8-3.6-1.9-7h3.8c-.1 3.4-1 5.8-1.9 7zm2.6-1.4a15 15 0 001.3-5.6h3a8 8 0 01-4.3 5.6z"/></svg>www.quorva.com</li>
    </ul>
    <address class="address">4172 Marlowe blvd<br>Fenwick Bay, OR 97411</address>
  </section>
</main>
</body>
</html>
```